Facial Tissue Brand Logo and Design

We would like you to design a Logo for the Facial Tissue Brand "Velora" along with the box design. The pack should indicate the pack size (150 x 2 ply). Also our company logo should be present (attached) along with a barcode. The box size dimensions should be 210mm (L) x 110mm (W) x 70mm (H). We are open to all kinds of nice designs which are attractive but not overdone. Happy designing!

UPDATE:
We appreciate the designs so far... but would also love to see more options in a simple and elegent design style that would look good on a table... please see attached below links for reference purpose:

www.pictovault-example.com/image-photo/cleaning-wipes-isolated-on-white-257770819

www.pictovault-example.com/image-photo/cleaning-wipes-isolated-on-white-155326937

www.pictovault-example.com/image-photo/delicate-female-hands-pulling-tissue-out-1330426586

Happy desgining!

We appreciate the designs so far.. but would like to to see some more options.

```html
<!DOCTYPE html>
<html lang="en">
<head>
<meta charset="utf-8">
<title>Velora — Packaging and Logo</title>
<link rel="stylesheet" href="https://fonts.googleapis.com/css2?family=Open+Sans:wght@400;500&family=Raleway:wght@400;500;600;700&display=swap">
<style>
  :root {
    --cream: #fcfdcb;
    --white: #ffffff;
    --forest: #3a5f18;
    --forest-deep: #365e17;
    --lime: #c2d64a;
    --yellow: #f0c81a;
    --brand: #d2c40c;
    --label-bg: #f4f4f1;
    --box-bg: #f1f1ef;
    --grey-text: #7b7b7b;
    --sky: #6aaedc;
    --peach: #f19a6b;
    --indigo: #3b3f9a;
  }
  * { box-sizing: border-box; margin: 0; padding: 0; }
  html, body { width: 1200px; height: 2166px; overflow: hidden; }
  body { position: relative; background: var(--white); font-family: "Raleway", sans-serif; }

  .section-title {
    position: absolute; left: 0; width: 1200px; text-align: center;
    font-family: "Open Sans", sans-serif; font-weight: 500; color: var(--forest);
    font-size: 66px; line-height: 1;
  }

  /* Packaging section */
  .packaging-section { position: absolute; left: 0; top: 0; width: 1200px; height: 942px; background: var(--cream); }
  .packaging-section .section-title { top: 38px; }

  .tissue-box {
    position: absolute; left: 126px; top: 276px; width: 938px; height: 491px;
    background: var(--box-bg); overflow: hidden;
  }
  .botanical-art { position: absolute; }
  .art-left {
    left: 0; top: 0; width: 290px; height: 491px;
    background: linear-gradient(160deg, #cfe07a 0%, #f3cf3a 45%, #7fae45 75%, #f2a57a 100%);
    border-radius: 0 60% 40% 0 / 0 30% 20% 0; opacity: .9;
  }
  .art-bottom {
    left: 260px; top: 380px; width: 420px; height: 111px;
    background: linear-gradient(90deg, #5c63b0 0%, #7bb6e0 45%, #b9d45a 100%);
    border-radius: 60px 60px 0 0; opacity: .85;
  }
  .art-right {
    left: 630px; top: 0; width: 308px; height: 491px;
    background: linear-gradient(200deg, #f3a882 0%, #c2d64a 35%, #a8cc4a 60%, #3f6b22 100%);
    border-radius: 45% 0 0 35% / 30% 0 0 25%; opacity: .92;
  }

  .box-brand {
    position: absolute; left: 0; top: 38px; width: 938px; text-align: center;
    font-family: "Raleway", sans-serif; font-weight: 500; font-size: 60px;
    color: var(--brand); line-height: 1; letter-spacing: 1px;
  }

  .product-label {
    position: absolute; left: 265px; top: 149px; width: 406px; height: 197px;
    background: var(--label-bg); border: 3px solid var(--forest); border-radius: 34px;
    box-shadow: 0 0 0 7px var(--box-bg);
    text-align: center;
  }
  .count-badge {
    position: absolute; top: 33px; background: var(--lime); color: #222;
    font-weight: 700; line-height: 1; padding: 3px 3px 2px; border-radius: 3px;
  }
  .count-badge .count-number { display: block; font-size: 19px; }
  .count-badge .count-unit { display: block; font-size: 7px; font-weight: 500; margin-top: 1px; }
  .badge-pulls { left: 19px; }
  .badge-ply { right: 25px; background: var(--yellow); padding: 3px 6px 2px; }

  .label-claim { margin-top: 14px; font-size: 30px; font-weight: 400; color: var(--yellow); line-height: 1; }
  .label-product { margin-top: 4px; font-size: 33px; font-weight: 700; color: var(--forest); line-height: 1; }
  .label-benefit { margin-top: 7px; font-size: 13px; font-weight: 500; color: var(--grey-text); }
  .label-copy {
    margin: 8px auto 0; width: 374px; border: 1.5px solid var(--lime);
    font-family: "Open Sans", sans-serif; font-size: 8px; line-height: 1.35; color: var(--grey-text);
    padding: 3px 8px;
  }
  .label-stripe {
    margin: 6px auto 0; width: 396px; height: 13px;
    background: linear-gradient(90deg, #eee27a, #f1e89a, #eee27a);
  }
  .label-count { margin-top: 6px; font-size: 13px; font-weight: 600; color: var(--brand); }

  /* Logo section */
  .logo-section { position: absolute; left: 0; top: 942px; width: 1200px; height: 820px; background: var(--white); }
  .logo-section .section-title { top: 72px; }
  .brand-mark {
    position: absolute; left: 0; width: 1200px; text-align: center;
    font-family: "Raleway", sans-serif; font-weight: 500; color: var(--brand); line-height: 1;
  }
  .logo-section .brand-mark { top: 330px; font-size: 170px; letter-spacing: 2px; }

  .logo-reverse { position: absolute; left: 0; top: 1762px; width: 1200px; height: 404px; background: var(--forest-deep); }
  .logo-reverse .brand-mark { top: 140px; font-size: 110px; letter-spacing: 1px; }
</style>
</head>
<body>

<section class="packaging-section">
  <h2 class="section-title">Packaging</h2>

  <div class="tissue-box">
    <div class="botanical-art art-left" role="img" aria-label="Botanical illustration of green, yellow and peach leaves with a yellow blob"></div>
    <div class="botanical-art art-bottom" role="img" aria-label="Botanical illustration of striped indigo, blue and lime leaves"></div>
    <div class="botanical-art art-right" role="img" aria-label="Botanical illustration of a lime blob with peach and dark green leaves"></div>

    <div class="box-brand">Velora</div>

    <div class="product-label">
      <div class="count-badge badge-pulls"><span class="count-number">150</span><span class="count-unit">PULLS</span></div>
      <div class="count-badge badge-ply"><span class="count-number">2</span><span class="count-unit">PLY</span></div>
      <p class="label-claim">hypoallergenic</p>
      <p class="label-product">FACIAL WIPES</p>
      <p class="label-benefit">Gentle Cleansing and Makeup Removal</p>
      <p class="label-copy">Lorem ipsum dolor sit amet, consectetur adipiscing elit, sed do eiusmod tempor<br>incididunt ut labore et dolore magna aliqua.</p>
      <div class="label-stripe" role="img" aria-label="Decorative diagonal stripe band"></div>
      <p class="label-count">30 Pre-Moistened Wipes</p>
    </div>
  </div>
</section>

<section class="logo-section">
  <h2 class="section-title">logo</h2>
  <div class="brand-mark">Velora</div>
</section>

<section class="logo-reverse">
  <div class="brand-mark">Velora</div>
</section>

</body>
</html>
```